Marlow Sail Works President Business Card Carbon fiber catamarans

Hi.. I need a new business card design.. I am the President of a high tech yacht builder. We build Carbon Fiber go fast catamarans... Maybe we use the file I am sharing to you as the back of the card.. We need to look cool and crisp ...

Target Market(s)

Affluent People who will purchase a cool yacht

Industry/Entity Type

Custom Yacht Builder

Contact Information for Business Card

Dean Pellway , President, 731.508.2164 USA

Font styles to use
Serif

Requirements
Must have
• the clean crisp cool feel
Nice to have
• clean and crisp
Should not have
• Bold ugly

```html
<!DOCTYPE html>
<html lang="en">
<head>
<meta charset="utf-8">
<title>Marlow Sail Works – Business Card</title>
<link href="https://fonts.googleapis.com/css2?family=Oswald:wght@500&family=Questrial&display=swap" rel="stylesheet">
<style>
  :root {
    --backdrop: #3a3a3a;
    --carbon-light: #2a2a2a;
    --carbon-dark: #0b0b0b;
    --silver-light: #e6e6e6;
    --silver-mid: #bdbdbd;
    --silver-dark: #8a8a8a;
    --text-light: #d9d9d9;
    --text-dark: #121212;
    --text-grey: #2a2a2a;
  }
  * { margin: 0; padding: 0; box-sizing: border-box; }
  html, body { width: 1125px; height: 1200px; overflow: hidden; }
  body {
    background: var(--backdrop);
    font-family: "Questrial", sans-serif;
    position: relative;
  }
  .card {
    position: absolute;
    left: 171px;
    width: 826px;
    height: 471px;
    overflow: hidden;
    box-shadow: 0 6px 18px rgba(0,0,0,.55);
  }
  .card--front { top: 106px; }
  .card--back { top: 624px; }
  .carbon-surface {
    position: absolute; inset: 0;
    background: radial-gradient(ellipse at 40% 35%, var(--carbon-light) 0%, var(--carbon-dark) 85%);
  }
  .swoosh { position: absolute; inset: 0; }
  .brand {
    position: absolute;
    display: flex; align-items: center; gap: 14px;
    color: var(--text-light);
    font-family: "Questrial", sans-serif;
    letter-spacing: 4px;
    text-transform: uppercase;
    white-space: nowrap;
  }
  .brand__mark {
    border-radius: 50%;
    border: 2px solid var(--silver-mid);
    flex: none;
  }
  .card--front .brand { left: 58px; top: 74px; font-size: 27px; }
  .card--front .brand__mark { width: 46px; height: 46px; }
  .address, .contact-list {
    position: absolute; left: 57px;
    color: var(--text-light);
    font-size: 21px; line-height: 26px;
  }
  .address { top: 180px; }
  .contact-list { top: 272px; list-style: none; }
  .contact-list li { display: flex; align-items: center; gap: 12px; }
  .contact-list svg { width: 18px; height: 18px; fill: var(--text-light); flex: none; }
  .holder {
    position: absolute; right: 36px; top: 380px;
    text-align: right;
  }
  .holder__name {
    font-family: "Oswald", sans-serif; font-weight: 500;
    font-size: 36px; line-height: 40px; letter-spacing: 1px;
    color: var(--text-dark);
  }
  .holder__title { font-size: 20px; color: var(--text-grey); }
  .card--back .brand {
    left: 0; right: 0; top: 205px; justify-content: center;
    font-size: 40px; letter-spacing: 6px;
  }
  .card--back .brand__mark { width: 64px; height: 64px; }
  .social {
    position: absolute; left: 0; right: 0; top: 393px;
    display: flex; justify-content: center; align-items: center; gap: 8px;
  }
  .social__rule { width: 100px; height: 1px; background: var(--silver-dark); margin: 0 8px; }
  .social__dot { width: 26px; height: 26px; border-radius: 50%; background: var(--silver-light); }
  .edge-line {
    position: absolute; left: 280px; right: 0; bottom: 4px; height: 2px;
    background: linear-gradient(90deg, transparent, var(--silver-dark));
  }
</style>
</head>
<body>

<section class="card card--front">
  <div class="carbon-surface" role="img" aria-label="Dark perforated carbon texture"></div>
  <svg class="swoosh" viewBox="0 0 826 471" preserveAspectRatio="none" aria-hidden="true">
    <defs>
      <linearGradient id="silverFill" x1="0" y1="1" x2="1" y2="0">
        <stop offset="0" stop-color="#f0f0f0"/>
        <stop offset="0.5" stop-color="#c4c4c4"/>
        <stop offset="1" stop-color="#9a9a9a"/>
      </linearGradient>
      <linearGradient id="silverEdge" x1="0" y1="1" x2="1" y2="0">
        <stop offset="0" stop-color="#ffffff"/>
        <stop offset="1" stop-color="#6e6e6e"/>
      </linearGradient>
    </defs>
    <path d="M 280 471 C 560 420 720 260 712 0 L 730 0 C 745 270 590 430 330 471 Z" fill="url(#silverEdge)"/>
    <path d="M 330 471 C 590 430 750 270 772 0 L 826 0 L 826 471 Z" fill="url(#silverFill)"/>
  </svg>

  <div class="brand"><span class="brand__mark"></span>Marlow Sail Works</div>

  <address class="address" style="font-style:normal">
    2918 Tidewater Lane<br>Anchorage<br>Alaska 34580
  </address>

  <ul class="contact-list">
    <li><svg viewBox="0 0 24 24"><path d="M6.6 10.8a15.5 15.5 0 0 0 6.6 6.6l2.2-2.2c.3-.3.7-.4 1-.2 1.1.4 2.3.6 3.6.6.6 0 1 .4 1 1V20c0 .6-.4 1-1 1A17 17 0 0 1 3 4c0-.6.4-1 1-1h3.5c.6 0 1 .4 1 1 0 1.3.2 2.5.6 3.6.1.3 0 .7-.2 1z"/></svg>731-508-2164</li>
    <li><svg viewBox="0 0 24 24"><path d="M7 1h10a2 2 0 0 1 2 2v18a2 2 0 0 1-2 2H7a2 2 0 0 1-2-2V3a2 2 0 0 1 2-2zm0 3v14h10V4z"/></svg>731-508-2170</li>
    <li><svg viewBox="0 0 24 24"><path d="M6 2h10l2 2v5H6zM3 10h18a1 1 0 0 1 1 1v7h-4v4H6v-4H2v-7a1 1 0 0 1 1-1zm5 6v4h8v-4z"/></svg>731-508-2199</li>
    <li><svg viewBox="0 0 24 24"><path d="M2 5h20v14H2zm2 2v.5l8 5 8-5V7l-8 5z"/></svg>name@Marlowsail.com</li>
    <li><svg viewBox="0 0 24 24"><path d="M12 2a10 10 0 1 0 0 20 10 10 0 0 0 0-20zm-1 17.9A8 8 0 0 1 4.1 10L9 15v1a2 2 0 0 0 2 2zm6.9-2.5A2 2 0 0 0 16 16h-1v-3a1 1 0 0 0-1-1H8v-2h2a1 1 0 0 0 1-1V7h2a2 2 0 0 0 2-2v-.4a8 8 0 0 1 2.9 12.8z"/></svg>www.Marlowsail.com</li>
  </ul>

  <div class="holder">
    <div class="holder__name">DEAN PELLWAY</div>
    <div class="holder__title">President</div>
  </div>
</section>

<section class="card card--back">
  <div class="carbon-surface" role="img" aria-label="Dark perforated carbon texture"></div>
  <div class="brand"><span class="brand__mark"></span>Marlow Sail Works</div>
  <div class="social" aria-label="Social channels">
    <span class="social__rule"></span>
    <span class="social__dot"></span>
    <span class="social__dot"></span>
    <span class="social__dot"></span>
    <span class="social__rule"></span>
  </div>
  <div class="edge-line"></div>
</section>

</body>
</html>
```